Larkspur Talent IT Recruiting firm needs a business card design for Recruiters, Sourcers, and Account

We need business cards that allow us to change all contact info, names, titles (Recruiter, Sourcer, Account Manager, Director, CEO, etc) per person since we have three offices, in three cities, Phoenix, Austin, and Las Vegas. We do recruiting and contractors for IT positions (Developers, Architects, Software Engineers, Security Engineers, Help Desk, DBAs, PMs, Scrum Masters, etc.) Our client companies are very diverse from Meridian 100 to silicone Valley type start-ups.

So, while we what hip, techie, and quirky, it still needs to be professional. Primary color we use is blue, with silver as a secondary color.

Target Market(s)

IT, Technology

Industry/Entity Type

Business

Contact Information for Business Card

Company name: Larkspur Talent, Inc.
Website: www.larkspurtalent.example
Logos for Careerloop, Blipster, and Myriada

Name, Title, Office Number, Cell Number, email

Font styles to use
Serif
Sans Serif

Colors
0455a3
d5d5d5

Requirements
Nice to have
• The grey I selected below is not necessary - but, would like silver included. I included a card design (File 3: LTI early trial example.jpg) that I had started on. It's very rough, and not quite what we're looking for, but what we did like is the logo, big, maybe a bit faded, off center, goes out of frame, etc. Still looking for other ideas - you are the pros! But, just an idea of a design element we liked.

```html
<!DOCTYPE html>
<html lang="en">
<head>
<meta charset="utf-8">
<title>Larkspur Talent – Business Card</title>
<link rel="stylesheet" href="https://fonts.googleapis.com/css2?family=Cinzel:wght@400&family=Marcellus&family=Open+Sans:wght@400;700&display=swap">
<style>
  :root {
    --brand-blue: #0455a3;
    --ink: #1c1c1c;
    --silver: #d5d5d5;
    --paper: #ffffff;
    --backdrop: #e9e9ea;
  }
  * { margin: 0; padding: 0; box-sizing: border-box; }
  html, body { width: 1200px; height: 904px; overflow: hidden; background: var(--backdrop); }
  .canvas { position: relative; width: 1200px; height: 904px; }

  .card {
    position: absolute; left: 250px; width: 700px; height: 400px;
    background: var(--paper); border-radius: 36px; overflow: hidden;
    box-shadow: 0 6px 18px rgba(0,0,0,.18);
  }
  .card--front { top: 40px; }
  .card--back { top: 464px; }

  .wordmark {
    position: absolute; left: 0; right: 0;
    display: flex; align-items: center; justify-content: center; gap: 16px;
  }
  .wordmark__dot { width: 50px; height: 50px; border-radius: 50%; background: var(--brand-blue); flex: none; }
  .wordmark__name {
    font-family: "Marcellus", serif; font-size: 52px; letter-spacing: 3px;
    color: var(--ink); line-height: 1; text-transform: uppercase; white-space: nowrap;
  }
  .tagline {
    position: absolute; left: 0; right: 0; text-align: center;
    font-family: "Cinzel", serif; font-size: 21px; letter-spacing: 4px; color: var(--ink);
    white-space: nowrap;
  }
  .card--front .wordmark { top: 120px; }
  .card--front .tagline { top: 200px; }
  .website-line {
    position: absolute; top: 270px; left: 0; right: 0; text-align: center;
    font-family: "Open Sans", sans-serif; font-size: 21px; letter-spacing: 2.5px; color: var(--ink);
  }

  .card--back .wordmark { top: 46px; }
  .card--back .tagline { top: 124px; }
  .person {
    position: absolute; top: 178px; left: 150px;
    font-family: "Open Sans", sans-serif; font-size: 17px; color: var(--ink); white-space: nowrap;
  }
  .person__name { font-weight: 700; font-size: 22px; color: var(--brand-blue); }

  .wave { position: absolute; left: 0; top: 0; width: 700px; height: 400px; }

  .socials {
    position: absolute; left: 34px; top: 300px;
    font-family: "Open Sans", sans-serif; font-size: 15px; color: var(--paper);
    list-style: none;
  }
  .socials li { display: flex; align-items: center; gap: 8px; height: 26px; }
  .socials__mark { width: 15px; height: 15px; border-radius: 50%; background: var(--paper); }

  .contacts {
    position: absolute; right: 60px; top: 316px; list-style: none;
    font-family: "Open Sans", sans-serif; font-size: 16px; color: var(--paper); text-align: right;
  }
  .contacts li { display: flex; align-items: center; justify-content: flex-end; gap: 8px; height: 25px; white-space: nowrap; }
  .contacts svg { width: 15px; height: 15px; flex: none; }
</style>
</head>
<body>
<main class="canvas">

  <section class="card card--front" aria-label="Card front">
    <div class="wordmark">
      <span class="wordmark__dot"></span>
      <span class="wordmark__name">Larkspur Talent</span>
    </div>
    <p class="tagline">Finding the Perfect Fit</p>
    <p class="website-line">www.larkspurtalent.example</p>
  </section>

  <section class="card card--back" aria-label="Card back">
    <svg class="wave" viewBox="0 0 700 400" aria-hidden="true">
      <path d="M0,215 C140,300 320,330 470,312 C570,300 640,292 700,294 L700,400 L0,400 Z" fill="var(--brand-blue)"/>
      <path d="M0,200 C140,292 320,318 470,300 C570,288 640,280 700,282" fill="none" stroke="var(--ink)" stroke-width="4"/>
      <path d="M0,190 C150,280 330,304 470,288 C570,276 640,270 700,272" fill="none" stroke="var(--brand-blue)" stroke-width="2"/>
    </svg>

    <div class="wordmark">
      <span class="wordmark__dot"></span>
      <span class="wordmark__name">Larkspur Talent</span>
    </div>
    <p class="tagline">Finding the Perfect Fit</p>
    <p class="person"><span class="person__name">Jordan Reeves,</span> First Touch Embassador</p>

    <ul class="socials">
      <li><span class="socials__mark"></span>@JordanReevesLT</li>
      <li><span class="socials__mark"></span>@JordanReevesLT</li>
    </ul>

    <ul class="contacts">
      <li>
        <svg viewBox="0 0 16 16"><circle cx="8" cy="8" r="7" fill="none" stroke="#fff" stroke-width="1.5"/><path d="M5 4.5l1.6-.4 1 2-1 .8c.5 1 1.2 1.8 2.2 2.3l.8-1 2 1-.4 1.6c-3 .3-6.4-3-6.2-6.3z" fill="#fff"/></svg>
        512-555-0147
      </li>
      <li>
        <svg viewBox="0 0 16 16"><rect x="1.5" y="4" width="13" height="9" fill="none" stroke="#fff" stroke-width="1.5"/><path d="M1.5 4l6.5 5 6.5-5" fill="none" stroke="#fff" stroke-width="1.5"/></svg>
        jordan@larkspurtalent.example
      </li>
      <li>
        <svg viewBox="0 0 16 16"><circle cx="8" cy="8" r="6.5" fill="none" stroke="#fff" stroke-width="1.4"/><ellipse cx="8" cy="8" rx="3" ry="6.5" fill="none" stroke="#fff" stroke-width="1.2"/><path d="M1.5 8h13" stroke="#fff" stroke-width="1.2"/></svg>
        www.larkspurtalent.example
      </li>
    </ul>
  </section>

</main>
</body>
</html>
```